Website Design for a Project Management Consulting Business

I have a logo design already and now I need a website.
I am a project manager and run my own consulting business.
Currently I am under contract with 3 major Vantage 400 companies. I'd like a website I can direct current and future clients.
My job is running IT projects and working with developers to deliver business priorities.
The website should be professional and clean - I work IT projects and would like to incorporate that into any theme.
I'd like the site to have several page or breakoff links - sections would include : about me, about my services, a page to display all of my certification badges, another page to talk about highlights from past projects and so on.
Looking for a collaborative experience.

Industry/Entity Type

Vantage 400 Consulting Firm - Project Management

Coding

Coded - Design and coding required

Number of Pages Required

1 page

Font styles to use
Serif

Colors
0094D4
00A9DD
6FCCEA
C7EBF8
E9F6FB
EE7325
F08F49
F5BC92
FAE3D3
FDF4ED

Requirements
Must have
• Sections that are a must: About Me (bio), About My Services, About my Certifications and Credentials, Experience on Past Projects,
Nice to have
• I have added the logo below - I'd like to use the logo and have it prominent ; should be professional and inviting

```html
<!DOCTYPE html>
<html lang="en">
<head>
<meta charset="utf-8">
<title>Meridian Project Partners LLC</title>
<link href="https://fonts.googleapis.com/css2?family=Michroma&family=Roboto:wght@400;500;700&display=swap" rel="stylesheet">
<style>
:root{
  --blue:#0094d4;
  --blue-2:#00a9dd;
  --navy:#0a3463;
  --navy-deep:#082b52;
  --navy-card:#0b325e;
  --orange:#ee7325;
  --grey-band:#e3e3e3;
  --soft:#f4f4f4;
  --text:#333;
  --muted:#666;
  --white:#fff;
}
*{box-sizing:border-box;margin:0;padding:0}
html,body{width:1200px;height:3637px;overflow:hidden}
body{position:relative;font-family:"Roboto",Arial,sans-serif;color:var(--text);background:var(--white)}
.abs{position:absolute}
.display{font-family:"Michroma","Roboto",sans-serif;font-weight:400;letter-spacing:1px}
/* header */
.site-header{position:absolute;top:0;left:0;width:1200px;height:90px;background:var(--white);border-top:4px solid var(--navy);z-index:3}
.brand{position:absolute;left:110px;top:20px;display:flex;align-items:center;gap:10px}
.brand-mark{width:38px;height:38px;border:3px solid var(--navy)}
.brand-name{font-family:"Roboto",sans-serif;font-weight:500;font-size:26px;color:var(--navy);letter-spacing:1px;line-height:1}
.nav{position:absolute;left:432px;top:36px;display:flex;gap:27px;font-size:15px;color:#222}
.nav a{color:inherit;text-decoration:none;position:relative}
.nav a.active{color:var(--blue)}
.nav a.active::after{content:"";position:absolute;left:0;right:0;bottom:-8px;height:2px;background:var(--blue)}
.login{position:absolute;left:989px;top:29px;width:99px;height:36px;background:var(--blue);color:#fff;font-size:15px;font-weight:500;display:flex;align-items:center;justify-content:center;gap:6px}
/* hero */
.hero{position:absolute;top:90px;left:0;width:1200px;height:640px;background:linear-gradient(90deg,#e6e6e6 0%,#dcdcdc 40%,#c9ccd0 100%)}
.hero-photo{position:absolute;left:480px;top:0;width:720px;height:640px;background:linear-gradient(135deg,#cfd2d6,#9aa2ab 50%,#dde0e3)}
.hero-title{position:absolute;left:110px;top:185px;font-size:34px;color:var(--blue)}
.hero-title span{color:var(--navy)}
.hero-copy{position:absolute;left:110px;top:240px;width:420px;font-size:16px;line-height:27px;color:#222}
.btn{display:inline-flex;align-items:center;gap:8px;background:var(--blue);color:#fff;font-weight:700;font-size:15px;text-transform:uppercase;text-decoration:none}
.hero .btn{position:absolute;left:110px;top:317px;height:48px;padding:0 25px}
/* about */
.portrait-ring{position:absolute;left:110px;top:830px}
.portrait{position:absolute;left:138px;top:774px;width:360px;height:450px;border-radius:0 0 180px 180px;background:linear-gradient(180deg,#d8dde4,#6f87a6);overflow:hidden}
.eyebrow{font-size:16px;font-weight:700;color:var(--blue);text-transform:uppercase;display:flex;align-items:center;gap:10px}
.eyebrow::before,.eyebrow.center::after{content:"";width:44px;height:2px;background:currentColor}
.about-text{position:absolute;left:603px;top:842px;width:485px}
.about-text h2{font-size:36px;color:var(--navy);margin:14px 0 24px}
.about-text p{font-size:14px;line-height:26px;color:var(--muted);text-align:justify;margin-bottom:13px}
.about-text .btn{height:42px;padding:0 14px;margin-top:18px}
.dot-arrow{width:14px;height:14px;border-radius:50%;background:#fff;color:var(--blue);font-size:10px;display:inline-flex;align-items:center;justify-content:center}
/* certifications */
.certs{position:absolute;top:1346px;left:0;width:1200px;height:460px;background:var(--soft)}
.center-head{position:absolute;left:0;width:1200px;text-align:center}
.center-head .eyebrow{justify-content:center}
.center-head h2{font-size:34px;margin-top:14px}
.certs h2{color:var(--navy)}
.cert-row{position:absolute;top:179px;left:103px;display:flex;gap:24px}
.cert-card{width:315px;height:77px;background:#fff;border-radius:40px;box-shadow:0 4px 12px rgba(0,0,0,.08);display:flex;align-items:center;gap:16px;padding-left:14px}
.cert-badge{width:64px;height:64px;border-radius:50%;flex:none}
.cert-card p{font-size:16px;font-weight:500;color:#222;line-height:23px}
/* services */
.services{position:absolute;top:1790px;left:0;width:1200px;height:640px;background:var(--navy)}
.services .eyebrow{color:var(--blue-2)}
.services h2{color:#fff}
.service-card{position:absolute;top:222px;width:325px;height:260px;background:var(--navy-card);border:1px solid #123f70;padding:76px 26px 0}
.service-card.featured{background:var(--orange);border-color:var(--orange)}
.service-icon{position:absolute;left:26px;top:-36px;width:71px;height:71px;background:var(--blue-2);display:flex;align-items:center;justify-content:center}
.service-card h3{font-size:17px;font-weight:700;color:#fff;margin-bottom:18px}
.service-card p{font-size:14px;line-height:25px;color:#dce6f1;margin-bottom:16px}
.service-card .more{font-size:14px;font-weight:700;color:var(--blue-2);display:flex;align-items:center;gap:8px;text-transform:uppercase}
.service-card.featured .more{color:#fff}
.service-card.featured p{color:#fff}
.service-card .more .dot-arrow{background:currentColor;color:var(--navy)}
/* projects */
.projects-text{position:absolute;left:110px;top:2588px;width:290px}
.projects-text h2{font-size:33px;line-height:44px;color:var(--navy);margin:14px 0 22px}
.projects-text .eyebrow::after{content:"";width:44px;height:2px;background:currentColor}
.projects-text p{font-size:14px;line-height:26px;color:var(--muted)}
.arrows{position:absolute;left:110px;top:2886px;display:flex;gap:14px}
.arrow-btn{width:48px;height:48px;border-radius:50%;background:#e6e6e6;display:flex;align-items:center;justify-content:center}
.project-photo{position:absolute;top:2545px;height:436px}
/* footer */
.footer{position:absolute;top:3200px;left:0;width:1200px;height:437px;background:var(--navy)}
.footer-brand{position:absolute;left:112px;top:192px;display:flex;align-items:center;gap:10px}
.footer-brand .brand-mark{border-color:#fff;width:34px;height:34px}
.footer-brand .brand-name{color:#fff;font-size:22px}
.f-col{position:absolute;top:100px;color:#fff}
.f-col h4{font-size:17px;font-weight:700;text-transform:uppercase;margin-bottom:10px}
.f-col h4::after{content:"";display:block;width:60px;height:2px;background:var(--orange);margin-top:12px}
.f-links li{list-style:none;font-size:12px;line-height:26px;padding-left:6px}
.f-contact li{list-style:none;display:flex;gap:14px;font-size:12px;line-height:19px;margin-bottom:14px}
.f-contact svg{flex:none;margin-top:2px}
.f-sub p{font-size:12px;line-height:20px;padding-left:6px;margin-bottom:14px;width:260px}
.sub-form{display:flex;width:252px;height:36px;margin-left:6px;border-radius:18px;overflow:hidden;background:#fff}
.sub-form span{flex:1;font-size:10px;color:#777;padding-left:14px;display:flex;align-items:center}
.sub-form b{width:48px;background:var(--blue);display:flex;align-items:center;justify-content:center}
.socials{display:flex;gap:10px;margin-top:16px;padding-left:2px}
.socials i{width:30px;height:30px;border-radius:50%;background:#fff;display:block}
.socials i.on{background:var(--blue-2)}
.bottom-bar{position:absolute;left:0;bottom:0;width:1200px;height:62px;background:var(--navy-deep);color:#fff;font-size:13px}
.bottom-bar .copy{position:absolute;left:110px;top:24px}
.bottom-bar .copy u{color:var(--blue-2)}
.bottom-bar .legal{position:absolute;left:843px;top:24px}
.bottom-bar .code{position:absolute;left:1132px;top:24px;font-size:11px}
</style>
</head>
<body>

<header class="site-header">
  <div class="brand"><span class="brand-mark"></span><span class="brand-name">MERIDIAN</span></div>
  <nav class="nav">
    <a class="active">Home</a><a>About Me</a><a>About My Services</a><a>Certification</a><a>Past Projects</a>
  </nav>
  <div class="login"><svg width="11" height="12" viewBox="0 0 11 12"><rect x="1" y="5" width="9" height="7" fill="#fff"/><path d="M3 5V3.5a2.5 2.5 0 0 1 5 0V5" stroke="#fff" stroke-width="1.6" fill="none"/></svg>Log In</div>
</header>

<section class="hero">
  <div class="hero-photo" role="img" aria-label="Overhead photo of business team reviewing charts around a white sofa and glass table"></div>
  <h1 class="hero-title display">MERIDIAN <span>LLC</span></h1>
  <p class="hero-copy">Lorem ipsum dolor sit amet, consectetur adipiscing incididunt ut labore dolore magna aliqua.</p>
  <a class="btn">Get Started</a>
</section>

<svg class="abs" style="left:0;top:640px" width="1200" height="170" viewBox="0 0 1200 170">
  <polygon points="0,84 1200,10 1200,170 0,170" fill="#fff"/>
  <polygon points="218,72 1200,0 1200,22 218,95" fill="var(--grey-band)"/>
  <polygon points="800,55 1200,32 1200,158" fill="var(--orange)"/>
</svg>

<svg class="portrait-ring" width="420" height="420" viewBox="0 0 420 420">
  <circle cx="209" cy="212" r="200" fill="none" stroke="#0a3463" stroke-width="20" stroke-dasharray="820 440" transform="rotate(60 209 212)"/>
  <circle cx="209" cy="212" r="200" fill="none" stroke="#0094d4" stroke-width="20" stroke-dasharray="520 740" transform="rotate(-140 209 212)"/>
</svg>
<div class="portrait" role="img" aria-label="Portrait photo of the consultant in a blue checked suit and tie"></div>

<section class="about-text">
  <div class="eyebrow">About Me</div>
  <h2 class="display">JORDAN HALE</h2>
  <p>Jordan Hale is the Owner of Meridian Project Partners, LLC and serves as Principal Lead Consultant on waterfall and agile contract opportunities.</p>
  <p>Meridian Project Partners, LLC has engaged on a contract basis with Vantage 400 companies across various industries including banking and credit unions, global supply chain, and international food distribution. Jordan Hale brings 12 years of experience</p>
  <a class="btn">Learn More <span class="dot-arrow">›</span></a>
</section>

<section class="certs">
  <div class="center-head" style="top:60px">
    <div class="eyebrow center">About My</div>
    <h2 class="display">CERTIFICATIONS AND CREDENTIALS</h2>
  </div>
  <div class="cert-row">
    <div class="cert-card"><span class="cert-badge" style="background:#f2ad2c"></span><p>Certified Agile Team Lead</p></div>
    <div class="cert-card"><span class="cert-badge" style="background:#ee7325"></span><p>Certified Agile Product Owner</p></div>
    <div class="cert-card"><span class="cert-badge" style="background:#f2ad2c"></span><p>Advanced - Certified Agile Team Lead</p></div>
  </div>
</section>

<svg class="abs" style="left:0;top:1645px" width="1200" height="160" viewBox="0 0 1200 160">
  <polygon points="0,0 390,100 0,124" fill="var(--orange)"/>
  <polygon points="0,136 968,62 968,86 0,150" fill="var(--grey-band)"/>
  <polygon points="0,152 1200,73 1200,160 0,160" fill="var(--navy)"/>
</svg>

<section class="services">
  <div class="center-head" style="top:44px">
    <div class="eyebrow center">What We Do</div>
    <h2 class="display">ABOUT MY SERVICES</h2>
  </div>
  <article class="service-card" style="left:87px">
    <div class="service-icon"><svg width="36" height="44" viewBox="0 0 36 44" fill="none" stroke="#fff" stroke-width="2"><rect x="4" y="8" width="28" height="34"/><path d="M10 16h4M22 16h4M10 24h4M22 24h4M14 42v-8h8v8"/></svg></div>
    <h3>Lorem ipsum dolor sit amet</h3>
    <p>Sed ut perspiciatis unde omnis iste natus sit voluptatem accusantium doloremque laudantium, totam rem aperiam,</p>
    <div class="more">Learn More <span class="dot-arrow">›</span></div>
  </article>
  <article class="service-card featured" style="left:438px">
    <div class="service-icon"><svg width="46" height="40" viewBox="0 0 46 40" fill="none" stroke="#fff" stroke-width="2"><rect x="4" y="6" width="38" height="26"/><path d="M10 14h14M10 20h10M30 14v12M36 18v8M2 36h42"/></svg></div>
    <h3>Lorem ipsum dolor sit amet</h3>
    <p>Sed ut perspiciatis unde omnis iste natus sit voluptatem accusantium doloremque laudantium, totam rem aperiam,</p>
    <div class="more">Learn More <span class="dot-arrow">›</span></div>
  </article>
  <article class="service-card" style="left:789px">
    <div class="service-icon"><svg width="44" height="44" viewBox="0 0 44 44" fill="none" stroke="#fff" stroke-width="2"><rect x="4" y="4" width="36" height="26"/><path d="M10 22l8-8 6 6 10-10M14 30l-4 10M30 30l4 10"/></svg></div>
    <h3>Lorem ipsum dolor sit amet</h3>
    <p>Sed ut perspiciatis unde omnis iste natus sit voluptatem accusantium doloremque laudantium, totam rem aperiam,</p>
    <div class="more">Learn More <span class="dot-arrow">›</span></div>
  </article>
</section>

<svg class="abs" style="left:0;top:2340px" width="1200" height="160" viewBox="0 0 1200 160">
  <polygon points="0,0 1200,0 1200,8 0,90" fill="var(--navy)"/>
  <polygon points="218,78 1200,8 1200,30 218,100" fill="var(--grey-band)"/>
  <polygon points="800,60 1200,36 1200,158" fill="var(--orange)"/>
</svg>

<section class="projects-text">
  <div class="eyebrow">Projects</div>
  <h2 class="display">EXPERIENCE ON PAST PROJECTS</h2>
  <p>Lorem ipsum dolor sit amet, consectetur adipiscing elit, sed do eiusmod tempor labore et dolore magna aliqua.</p>
</section>
<div class="arrows">
  <span class="arrow-btn"><svg width="20" height="12" viewBox="0 0 20 12" fill="none" stroke="#333" stroke-width="1.6"><path d="M19 6H2M7 1L2 6l5 5"/></svg></span>
  <span class="arrow-btn"><svg width="20" height="12" viewBox="0 0 20 12" fill="none" stroke="#333" stroke-width="1.6"><path d="M1 6h17M13 1l5 5-5 5"/></svg></span>
</div>
<div class="project-photo" style="left:432px;width:287px;background:linear-gradient(160deg,#c9b89a,#7b8a99)" role="img" aria-label="Photo of two colleagues discussing a document in an office"></div>
<div class="project-photo" style="left:736px;width:286px;background:linear-gradient(160deg,#c7a27d,#8aa3b4)" role="img" aria-label="Photo of two colleagues reviewing a tablet together"></div>
<div class="project-photo" style="left:1039px;width:161px;background:linear-gradient(160deg,#d7d9dc,#4a5461)" role="img" aria-label="Photo of a smiling businessman in a dark suit"></div>

<svg class="abs" style="left:0;top:3085px" width="1200" height="130" viewBox="0 0 1200 130">
  <polygon points="0,0 390,105 0,128" fill="var(--orange)"/>
  <polygon points="0,118 968,60 968,84 0,130" fill="var(--grey-band)"/>
  <polygon points="0,128 1200,70 1200,130" fill="var(--navy)"/>
</svg>

<footer class="footer">
  <div class="footer-brand"><span class="brand-mark"></span><span class="brand-name">MERIDIAN</span></div>
  <div class="f-col" style="left:387px">
    <h4>Quick Links</h4>
    <ul class="f-links"><li>Home</li><li>About Me</li><li>About My Services</li><li>Certification</li><li>Past Projects</li><li>Contact Us</li></ul>
  </div>
  <div class="f-col" style="left:545px">
    <h4>Contact Us</h4>
    <ul class="f-contact">
      <li><svg width="12" height="12" viewBox="0 0 12 12"><path d="M2 1l3 2-1 2a6 6 0 0 0 3 3l2-1 2 3-2 1C5 10 2 7 1 3z" fill="#fff"/></svg>+1 555-014-2290</li>
      <li><svg width="12" height="10" viewBox="0 0 12 10"><rect width="12" height="10" fill="#fff"/><path d="M0 0l6 5 6-5" stroke="#0a3463" fill="none"/></svg>info@meridianprojectpartners.com</li>
      <li><svg width="10" height="13" viewBox="0 0 10 13"><path d="M5 13S0 7 0 5a5 5 0 0 1 10 0c0 2-5 8-5 8z" fill="#fff"/><circle cx="5" cy="5" r="2" fill="#0a3463"/></svg>Lorem ipsum dolor sit amet, adipiscing<br>elit, sed do eiusmod tempor</li>
      <li><svg width="12" height="12" viewBox="0 0 12 12"><rect x="1" y="3" width="10" height="9" fill="#fff"/><rect x="3" y="0" width="6" height="4" fill="#fff"/></svg>555-014-7731</li>
    </ul>
  </div>
  <div class="f-col f-sub" style="left:831px">
    <h4>Subscribe To Our Blog</h4>
    <p>Sign up today to get resources on how to attract and retain more customers!</p>
    <div class="sub-form"><span>✉&nbsp; Email Address</span><b><svg width="14" height="14" viewBox="0 0 14 14"><path d="M0 6L14 0 10 14 7 8z" fill="#fff"/></svg></b></div>
    <div class="socials"><i></i><i class="on"></i><i></i><i></i></div>
  </div>
  <div class="bottom-bar">
    <span class="copy">Copyright© 2022 &nbsp;<u>Meridian Project Partners llc</u> &nbsp;|&nbsp; All Rights Reserved</span>
    <span class="legal">Terms and Conditions &nbsp;&nbsp;|&nbsp;&nbsp; Privacy Policy</span>
    <span class="code">C37</span>
  </div>
</footer>

</body>
</html>
```